UX - Need some screens design for a Skill Assessment Application

I am building an app to carry out skill assessments. Depending on how the assessment is configured, it may have one or more parts
1. Question based assessment (Multiple Choice, True False, Fill in the blanks"
2. Endorsement by two colleagues - A screen that allows user to pick colleagues based on search and shows the status of pending requests
3. A written submission - a page that explains the format of the submission and a file upload
As each assessment can be configured with or without any of the steps, the assessment UI must be such that these areas get hidden/displayed based on configuration.
Colour codes to be used can be #0e78bb and #ffffff
There will also be a start screen (instructions) and an end screen (results)
Target Market(s)
Enterprise software
Number of Pages Required
4 page

```html
<!DOCTYPE html>
<html lang="en">
<head>
<meta charset="utf-8">
<title>Assessments Dashboard</title>
<link href="https://fonts.googleapis.com/css2?family=Inter:wght@400;500;600;700&display=swap" rel="stylesheet">
<style>
:root{
  --brand:#0e78bb;
  --band:#0457ae;
  --band-card:#1b69bb;
  --band-line:#2a6ab8;
  --white:#ffffff;
  --teal:#12a09a;
  --page:#f5f6f8;
  --ink:#222831;
  --muted:#555b63;
  --chip:#e8e9eb;
  --toast-text:#e9fbfa;
  --soft:#bcd3ee;
}
*{box-sizing:border-box;margin:0;padding:0}
html,body{width:1200px;height:771px;overflow:hidden}
body{font-family:"Inter",sans-serif;background:var(--page);color:var(--ink);position:relative}
.hero{position:absolute;left:0;top:0;width:1200px;height:288px;background:var(--band)}
.topnav{position:absolute;left:0;top:0;width:1200px;height:43px;border-bottom:1px solid var(--band-line)}
.brand{position:absolute;left:71px;top:12px;display:flex;align-items:center;gap:9px;color:var(--white);font-weight:600;font-size:14px}
.brand-dot{width:18px;height:18px;border-radius:50%;background:var(--white)}
.nav-links a{position:absolute;top:15px;font-size:12.5px;color:#d6e3f4;text-decoration:none;white-space:nowrap}
.nav-links a.active{color:var(--white);font-weight:600}
.nav-links a.active::after{content:"";position:absolute;left:0;right:0;top:22px;height:3px;background:#41a8e6}
.nav-icon{position:absolute;top:12px}
.avatar{border-radius:50%;background:linear-gradient(135deg,#3a4b6a,#c9a28a)}
.avatar-sm{position:absolute;left:1101px;top:8px;width:28px;height:28px;border:2px solid var(--white)}
.toast{position:absolute;left:436px;top:51px;width:329px;height:37px;background:var(--teal);border-radius:3px;display:flex;align-items:center;padding-left:20px;gap:12px;color:var(--toast-text);font-size:11.3px;white-space:nowrap}
.avatar-lg{position:absolute;left:58px;top:72px;width:42px;height:42px}
.welcome{position:absolute;left:121px;top:75px;font-size:12px;color:var(--soft)}
.user-name{position:absolute;left:121px;top:92px;font-size:17px;font-weight:500;color:var(--white);white-space:nowrap}
.btn-create{position:absolute;left:965px;top:75px;width:178px;height:35px;background:var(--brand);border-radius:3px;color:var(--white);font-size:11.5px;font-weight:500;display:flex;align-items:center;justify-content:center;gap:8px;white-space:nowrap}
.summary-label{position:absolute;left:57px;top:141px;font-size:14px;color:var(--white);font-weight:500}
.stat{position:absolute;top:171px;width:260px;height:90px;background:var(--band-card);border-radius:3px;color:var(--white)}
.stat-icon{position:absolute;left:14px;top:14px;width:34px;height:34px;border-radius:3px;background:#3b80c8;display:flex;align-items:center;justify-content:center}
.stat-num{position:absolute;left:65px;top:22px;font-size:17px;font-weight:500}
.stat-title{position:absolute;left:65px;top:48px;font-size:12.5px;font-weight:500}
.stat-note{position:absolute;left:65px;top:67px;font-size:9.5px;color:var(--soft);white-space:nowrap}
.section-title{position:absolute;left:71px;top:309px;font-size:17px;font-weight:600;color:var(--ink)}
.tabs{position:absolute;left:71px;top:349px;display:flex;height:31px;font-size:12px}
.tab{display:flex;align-items:center;padding:0 17px;background:var(--chip);color:var(--muted);border-radius:0 3px 3px 0}
.tab.active{background:var(--brand);color:var(--white);border-radius:3px 0 0 3px}
.tab b{margin-left:4px;font-weight:600}
.view-toggle{position:absolute;top:355px}
.card{position:absolute;top:401px;width:340px;height:167px;background:var(--white);border-radius:3px;box-shadow:0 1px 3px rgba(0,0,0,.05)}
.card-id{position:absolute;left:21px;top:21px;font-size:12.5px;color:var(--muted)}
.card-title{position:absolute;left:21px;top:45px;font-size:12.5px;color:var(--brand);white-space:nowrap}
.card-menu{position:absolute;right:20px;top:21px}
.meta{position:absolute;top:72px}
.meta .label{font-size:9.5px;color:var(--ink);letter-spacing:.2px}
.meta .value{font-size:12.5px;color:var(--muted);margin-top:5px}
.chips{position:absolute;left:21px;top:123px;display:flex;gap:7px}
.chip{height:24px;border-radius:12px;background:var(--chip);color:var(--muted);font-size:12px;display:flex;align-items:center;gap:6px;padding:0 9px}
.tick{width:13px;height:13px;border-radius:50%;background:var(--teal);display:flex;align-items:center;justify-content:center}
</style>
</head>
<body>
<header class="hero">
  <nav class="topnav">
    <div class="brand"><span class="brand-dot"></span>Quorvane</div>
    <div class="nav-links">
      <a class="active" href="#" style="left:488px">Assessments</a>
      <a href="#" style="left:588px">Colleagues</a>
      <a href="#" style="left:671px">Results</a>
    </div>
    <svg class="nav-icon" style="left:1029px" width="18" height="18" viewBox="0 0 24 24" fill="none" stroke="#fff" stroke-width="1.6"><path d="M6 16V11a6 6 0 0112 0v5l2 2H4z"/><path d="M10 20a2 2 0 004 0"/></svg>
    <svg class="nav-icon" style="left:1064px" width="18" height="18" viewBox="0 0 24 24" fill="none" stroke="#fff" stroke-width="1.6"><circle cx="12" cy="12" r="3"/><path d="M12 2l2 3 3.5-.8.8 3.5 3 2-1.8 3 1.8 3-3 2-.8 3.5-3.5-.8-2 3-2-3-3.5.8-.8-3.5-3-2 1.8-3-1.8-3 3-2 .8-3.5L10 5z"/></svg>
    <div class="avatar avatar-sm" role="img" aria-label="User profile photo"></div>
  </nav>

  <div class="toast">
    <svg width="15" height="15" viewBox="0 0 16 16"><circle cx="8" cy="8" r="8" fill="#fff"/><path d="M4.5 8.2l2.3 2.2 4.7-4.6" stroke="#12a09a" stroke-width="1.8" fill="none"/></svg>
    The assessment has been successfully submitted.
  </div>

  <div class="avatar avatar-lg" role="img" aria-label="User profile photo"></div>
  <p class="welcome">Welcome back!</p>
  <h1 class="user-name">Maya R. Lestari</h1>

  <div class="btn-create">
    <svg width="13" height="13" viewBox="0 0 16 16" fill="none" stroke="#fff" stroke-width="1.3"><path d="M3 1.5h7l2.5 2.5v4M3 1.5v13h5"/><path d="M5 5.5h5M5 8h3"/><circle cx="11.5" cy="11.5" r="2.5"/><path d="M13.3 13.3l1.5 1.5"/></svg>
    Create New Assessment
  </div>

  <h2 class="summary-label">Summary</h2>

  <section class="stat" style="left:57px">
    <div class="stat-icon"><svg width="22" height="22" viewBox="0 0 24 24" fill="none" stroke="#fff" stroke-width="1.5"><path d="M5 3h10l3 3v6M5 3v18h7"/><path d="M8 8h7M8 11h4M8 14h3"/><circle cx="16.5" cy="16.5" r="3.5"/><path d="M15 16.5l1.2 1.2 2-2"/></svg></div>
    <div class="stat-num">7</div><div class="stat-title">My Assessments</div><div class="stat-note">3 pending</div>
  </section>
  <section class="stat" style="left:333px">
    <div class="stat-icon"><svg width="22" height="22" viewBox="0 0 24 24" fill="none" stroke="#fff" stroke-width="1.5"><path d="M12 2l1.5 3 3 .4-2.2 2.1.5 3-2.8-1.5-2.8 1.5.5-3L7.5 5.4l3-.4z"/><path d="M3 13h3v8H3zM6 14h4l4 1.5a1.3 1.3 0 010 2.5H10M6 20h7l7-4a1.4 1.4 0 00-1.5-2.3L14 16"/></svg></div>
    <div class="stat-num">4</div><div class="stat-title">Endorsements</div><div class="stat-note">1 pending</div>
  </section>
  <section class="stat" style="left:608px">
    <div class="stat-icon"><svg width="22" height="22" viewBox="0 0 24 24" fill="none" stroke="#fff" stroke-width="1.5"><circle cx="6.5" cy="6" r="2.5"/><circle cx="17.5" cy="6" r="2.5"/><circle cx="12" cy="12" r="2.5"/><path d="M2 14a4.5 4.5 0 019 0M13 14a4.5 4.5 0 019 0M7 21a5 5 0 0110 0"/></svg></div>
    <div class="stat-num">11</div><div class="stat-title">Colleagues</div><div class="stat-note">Last updated on May 23, 2024</div>
  </section>
  <section class="stat" style="left:883px">
    <div class="stat-icon"><svg width="22" height="22" viewBox="0 0 24 24" fill="none" stroke="#fff" stroke-width="1.5"><path d="M12 14V3M8 7l4-4 4 4"/><path d="M3 12v8h18v-8M3 15h5l1.5 2h5L16 15h5"/></svg></div>
    <div class="stat-num">7</div><div class="stat-title">Submissions</div><div class="stat-note">Last submit on May 23, 2024</div>
  </section>
</header>

<main>
  <h2 class="section-title">Assessments</h2>
  <div class="tabs">
    <div class="tab active">Pending<b>2</b></div>
    <div class="tab">Completed<b>5</b></div>
  </div>
  <svg class="view-toggle" style="left:1075px" width="20" height="20" viewBox="0 0 20 20" fill="none" stroke="#0e78bb" stroke-width="1.5"><path d="M6 4h13M6 10h13M6 16h13M1 4h2M1 10h2M1 16h2"/></svg>
  <svg class="view-toggle" style="left:1111px" width="19" height="19" viewBox="0 0 20 20" fill="none" stroke="#666" stroke-width="1.5"><rect x="1" y="1" width="7" height="7"/><rect x="12" y="1" width="7" height="7"/><rect x="1" y="12" width="7" height="7"/><rect x="12" y="12" width="7" height="7"/></svg>

  <article class="card" style="left:71px">
    <div class="card-id">1723091983</div>
    <div class="card-title">Application Design Capabilities</div>
    <svg class="card-menu" width="4" height="16" viewBox="0 0 4 16" fill="#444"><circle cx="2" cy="2" r="1.7"/><circle cx="2" cy="8" r="1.7"/><circle cx="2" cy="14" r="1.7"/></svg>
    <div class="meta" style="left:21px"><div class="label">PUBLISHED ON</div><div class="value">20/05/2024</div></div>
    <div class="meta" style="left:146px"><div class="label">DUE DATE</div><div class="value">24/05/2024</div></div>
    <div class="chips"><span class="chip">Quiz</span><span class="chip">Endorsement</span><span class="chip">Submission</span></div>
  </article>

  <article class="card" style="left:430px">
    <div class="card-id">1723091983</div>
    <div class="card-title">Sales Representative Assessments</div>
    <svg class="card-menu" width="4" height="16" viewBox="0 0 4 16" fill="#444"><circle cx="2" cy="2" r="1.7"/><circle cx="2" cy="8" r="1.7"/><circle cx="2" cy="14" r="1.7"/></svg>
    <div class="meta" style="left:21px"><div class="label">PUBLISHED ON</div><div class="value">20/05/2024</div></div>
    <div class="meta" style="left:146px"><div class="label">DUE DATE</div><div class="value">24/05/2024</div></div>
    <div class="chips">
      <span class="chip">Quiz<span class="tick"><svg width="8" height="8" viewBox="0 0 10 10"><path d="M2 5.2l2 2 4-4" stroke="#fff" stroke-width="1.6" fill="none"/></svg></span></span>
      <span class="chip">Endorsement<span class="tick"><svg width="8" height="8" viewBox="0 0 10 10"><path d="M2 5.2l2 2 4-4" stroke="#fff" stroke-width="1.6" fill="none"/></svg></span></span>
      <span class="chip">Submission</span>
    </div>
  </article>
</main>
</body>
</html>
```